BOOK COVER for THE IRONCLAD FOUNDER

I am publishing my first book and need to nail the cover. The cover should feature my picture as this is a major branding play.
TITLE: The Ironclad Founder.
SUBTITLE: Forging A Lasting Company Heritage.
BOOK DESCRIPTION: "The Ironclad Founder," presents a comprehensive approach to building resilient and sustainable businesses. The book emphasizes the inevitability of challenges in the business world and stresses the importance of resilience in facing adversity. It highlights the concept of "Ironcladding" a business, drawing inspiration from the safety glass used in car windshields, which doesn't shatter upon impact​​.

The book identifies two primary types of business owners: "CAPTIVES," who are overwhelmed and cannot take a break from their businesses without facing chaos, and "IRONCLAD" entrepreneurs, who have established systems and processes, clear goals, and can step away from their businesses without encountering problems​​. It raises critical questions about why some business owners become "CAPTIVES" while others achieve a "IRONCLAD" state and explores the transition from one to the other​​.

Vantor points out that many well-intentioned business founders often lack a comprehensive roadmap or blueprint, leading to vulnerabilities in their businesses​​. Reflecting on his own journey from being a "CAPTIVE" to becoming "IRONCLAD," Vantor shares insights from his experiences and the lessons he learned along the way​​.

The book addresses the legal aspects of businesses, an often overlooked area in entrepreneurial literature, providing readers with a roadmap and the necessary legal systems and structures to build a "IRONCLAD" business​​. This approach led to the development of Vantor's Keystone Counsel Mentoring Plan and the Ironclad Method​​.

Vantor encourages business owners to shift their paradigm, viewing lawyers as primary care providers for their businesses rather than turning to them only in emergencies​​. "The Ironclad Founder" is an invitation to make this paradigm shift and provides a roadmap for becoming a resilient and successful entrepreneur​​.

Target Market(s)

Small business owners from Start-up to $10 Million

Industry/Entity Type

Legal / Entrepreneurship

Font styles to use
Serif

Colors
0054AA
0677BA
7BADD7
CADEEF
E8F1F8

Requirements
Must have
• I am publishing my first book and need to nail the cover. The cover should feature my picture as this is a major branding play. The foreward has been written by Dale Pruncey. This needs to be included in the cover.

```html
<!DOCTYPE html>
<html lang="en">
<head>
<meta charset="utf-8">
<title>The Ironclad Founder — Book Cover Spread</title>
<link rel="stylesheet" href="https://fonts.googleapis.com/css2?family=Cinzel:wght@400;500&family=Tinos:ital@1&family=Oswald:wght@300&family=Montserrat:wght@400&display=swap">
<style>
  :root {
    --royal: #0054AA;
    --azure: #0677BA;
    --sky: #7BADD7;
    --mist: #CADEEF;
    --frost: #E8F1F8;
    --navy: #1A2F6B;
    --backdrop: #9DBCE0;
    --white: #FFFFFF;
  }
  * { margin: 0; padding: 0; box-sizing: border-box; }
  html, body { width: 1200px; height: 829px; overflow: hidden; background: var(--backdrop); }

  .spread {
    position: absolute; left: 40px; top: 16px;
    width: 1120px; height: 796px;
    background: var(--royal);
    overflow: hidden;
  }

  /* Back cover */
  .back-cover { position: absolute; left: 0; top: 0; width: 525px; height: 796px; }
  .back-photo {
    position: absolute; left: 14px; top: 503px; width: 511px; height: 293px;
    background:
      radial-gradient(ellipse at 50% 55%, rgba(26,47,107,0.9) 0%, rgba(26,47,107,0.55) 35%, rgba(0,84,170,0) 70%),
      linear-gradient(180deg, rgba(0,84,170,0) 0%, rgba(122,88,60,0.35) 70%, rgba(0,84,170,0.2) 100%);
  }
  .blurb {
    position: absolute; left: 59px; top: 44px; width: 443px;
    font-family: "Tinos", "Times New Roman", serif; font-style: italic;
    font-size: 14px; line-height: 16.7px; color: var(--white);
    text-align: justify;
  }
  .blurb p + p { margin-top: 16.7px; }
  .blurb .closing { margin-left: 165px; text-align: right; }

  /* Spine */
  .spine {
    position: absolute; left: 525px; top: 0; width: 68px; height: 796px;
    background: var(--royal);
  }
  .spine-title {
    position: absolute; left: 0; top: 44px; width: 68px; height: 440px;
    display: flex; justify-content: center; align-items: flex-start;
  }
  .spine-title span {
    writing-mode: vertical-rl;
    font-family: "Cinzel", Georgia, serif; font-weight: 500; font-size: 25px; letter-spacing: 0.02em;
    color: var(--white); white-space: nowrap;
  }
  .spine-subtitle {
    position: absolute; left: 0; top: 496px; width: 68px;
    display: flex; justify-content: center;
  }
  .spine-subtitle span {
    writing-mode: vertical-rl;
    font-family: "Oswald", "Arial Narrow", sans-serif; font-weight: 300;
    font-size: 14px; line-height: 17px; color: var(--white); text-transform: uppercase;
  }
  .spine-author {
    position: absolute; left: 0; top: 660px; width: 68px; height: 136px;
    background: var(--frost);
    display: flex; justify-content: center; align-items: flex-start; padding-top: 8px;
  }
  .spine-author span {
    writing-mode: vertical-rl;
    font-family: "Cinzel", Georgia, serif; font-size: 24px; line-height: 28px;
    color: var(--royal); text-transform: uppercase;
  }

  /* Front cover */
  .front-cover {
    position: absolute; left: 593px; top: 0; width: 527px; height: 796px;
    background: linear-gradient(200deg, var(--azure) 0%, var(--royal) 45%, var(--royal) 100%);
  }
  .portrait {
    position: absolute; left: 40px; top: 60px; width: 420px; height: 540px;
    border-radius: 46% 46% 14% 14% / 28% 28% 8% 8%;
    background: linear-gradient(180deg, rgba(202,222,239,0.18) 0%, rgba(26,47,107,0.7) 40%, rgba(26,47,107,0.85) 100%);
  }
  .author-name {
    position: absolute; left: 0; top: 28px; width: 527px; text-align: center;
    font-family: "Cinzel", Georgia, serif; font-weight: 400; font-size: 44px; letter-spacing: 0.12em;
    color: var(--white); text-shadow: 2px 3px 4px rgba(10,20,60,0.6);
  }
  .title-block { position: absolute; left: 36px; top: 552px; color: var(--white); }
  .title-lead {
    font-family: "Cinzel", Georgia, serif; font-size: 28px; line-height: 28px;
    text-shadow: 2px 3px 4px rgba(10,20,60,0.6);
  }
  .title-main {
    font-family: "Cinzel", Georgia, serif; font-weight: 400; font-size: 58px; line-height: 56px;
    text-shadow: 2px 3px 4px rgba(10,20,60,0.6);
  }
  .subtitle {
    margin-top: 2px;
    font-family: "Oswald", "Arial Narrow", sans-serif; font-weight: 300;
    font-size: 29px; line-height: 32px; text-transform: uppercase;
  }
  .foreword {
    position: absolute; left: 36px; top: 732px; width: 446px; height: 20px;
    background: linear-gradient(90deg, var(--royal) 0%, var(--mist) 25%, var(--frost) 60%, var(--sky) 85%, rgba(0,84,170,0) 100%);
    font-family: "Montserrat", Arial, sans-serif; font-size: 13px; line-height: 20px;
    color: var(--navy); text-align: center;
  }
</style>
</head>
<body>
  <main class="spread">
    <section class="back-cover">
      <div class="back-photo" role="img" aria-label="Photo of the author seated on a lounge sofa in a navy suit"></div>
      <div class="blurb">
        <p>"The Ironclad Founder," presents a comprehensive approach to building resilient and sustainable businesses. The book emphasizes the inevitability of challenges in the business world and stresses the importance of resilience in facing adversity. It highlights the concept of "Ironcladding" a business, drawing inspiration from the safety glass used in car windshields, which doesn't shatter upon impact.</p>
        <p>The book identifies two primary types of business owners: "CAPTIVES," who are overwhelmed and cannot take a break from their businesses without facing chaos, and "IRONCLAD" entrepreneurs, who have established systems and processes, clear goals, and can step away from their businesses without encountering problems. It raises critical questions about why some business owners become "CAPTIVES" while others achieve an "IRONCLAD" state and explores the transition from one to the other.</p>
        <p>Vantor points out that many well-intentioned business founders often lack a comprehensive roadmap or blueprint, leading to vulnerabilities in their businesses. Reflecting on his own journey from being a "CAPTIVE" to becoming "IRONCLAD," Vantor shares insights from his experiences and the lessons he learned along the way.</p>
        <p>The book addresses the legal aspects of businesses, an often overlooked area in entrepreneurial literature, providing readers with a roadmap and the necessary legal systems and structures to build an "IRONCLAD" business. This approach led to the development of Vantor's Keystone Counsel Mentoring Plan and the Ironclad Method.</p>
        <p class="closing">Vantor encourages business owners to shift their paradigm, viewing lawyers as primary care providers for their businesses rather than turning to them only in emergencies. "The Ironclad Founder" is an invitation to make this paradigm shift and provides a roadmap for becoming a resilient and successful entrepreneur.</p>
      </div>
    </section>

    <section class="spine">
      <div class="spine-title"><span>THE IRONCLAD FOUNDER</span></div>
      <div class="spine-subtitle"><span>Forging A Lasting<br>Company Heritage</span></div>
      <div class="spine-author"><span>Grant<br>Vantor</span></div>
    </section>

    <section class="front-cover">
      <div class="portrait" role="img" aria-label="Portrait of the author with arms crossed, wearing a navy suit, in front of a glass building"></div>
      <h2 class="author-name">GRANT VANTOR</h2>
      <div class="title-block">
        <div class="title-lead">The</div>
        <h1 class="title-main">IRONCLAD<br>FOUNDER</h1>
        <p class="subtitle">Forging A Lasting Company Heritage</p>
      </div>
      <p class="foreword">The foreward has been written by Dale Pruncey</p>
    </section>
  </main>
</body>
</html>
```